Need Business Card for our Real Estate Business with Sales Executive's Picture

PANTONE 484 C ( RED)

PANTONE 2766 C ( BLUE

Industry/Entity Type

Real Estate

Contact Information for Business Card

Name, Mobile, email, & picture of Person
Agency Phone, address, Web address

Requirements
Must have
• Our Logo Colours, Agent Picture,

```html
<!DOCTYPE html>
<html lang="en">
<head>
<meta charset="utf-8">
<title>Meridian Real Estate – Business Cards</title>
<link rel="stylesheet" href="https://fonts.googleapis.com/css2?family=Work+Sans:wght@400;500;600&display=swap">
<style>
  :root {
    --navy: #14204f;
    --navy-light: #1f2d66;
    --red: #7a1a26;
    --white: #ffffff;
    --backdrop: #4a4541;
    --photo-a: #c9cbd6;
    --photo-b: #2c3f86;
  }
  * { margin: 0; padding: 0; box-sizing: border-box; }
  html, body {
    width: 1200px; height: 930px; overflow: hidden;
    background: var(--backdrop);
    font-family: "Work Sans", Arial, sans-serif;
  }
  .canvas { position: relative; width: 1200px; height: 930px; }
  .card {
    position: absolute; width: 560px; height: 320px; overflow: hidden;
    box-shadow: 0 10px 24px rgba(0,0,0,.35);
  }
  .card--back {
    left: 90px; top: 110px;
    background: linear-gradient(135deg, var(--navy) 0%, var(--navy-light) 55%, var(--navy) 100%);
    display: flex; align-items: center; justify-content: center;
  }
  .card--front { left: 550px; top: 490px; background: var(--white); }
  .card__art { position: absolute; inset: 0; }

  .wordmark { display: flex; flex-direction: column; align-items: center; color: var(--white); }
  .wordmark__row { display: flex; align-items: center; gap: 12px; }
  .wordmark__square { width: 14px; height: 14px; background: currentColor; }
  .wordmark__name { font-weight: 500; font-size: 44px; letter-spacing: 6px; line-height: 1; }
  .wordmark__sub {
    margin-top: 8px; padding-top: 6px; border-top: 1px solid currentColor;
    font-weight: 500; font-size: 11px; letter-spacing: 4px;
  }
  .card--front .wordmark {
    position: absolute; right: 36px; top: 34px; color: var(--navy);
  }
  .card--front .wordmark__name { font-size: 30px; letter-spacing: 4px; }
  .card--front .wordmark__square { width: 10px; height: 10px; background: var(--red); }
  .card--front .wordmark__sub { font-size: 10px; letter-spacing: 3px; }

  .agent { position: absolute; left: 150px; top: 220px; color: var(--white); }
  .agent__name { font-weight: 600; font-size: 19px; letter-spacing: .5px; line-height: 1.2; }
  .agent__role { font-size: 12px; margin-top: 2px; line-height: 1.2; }
  .address {
    position: absolute; left: 150px; top: 272px;
    color: var(--white); font-size: 11px; line-height: 1.35;
  }

  .contacts {
    position: absolute; right: 22px; top: 180px; list-style: none;
    color: var(--white); font-size: 12px; line-height: 1.45; text-align: right;
  }
  .contacts li { display: flex; align-items: center; justify-content: flex-end; gap: 8px; }
  .contacts svg { width: 11px; height: 11px; fill: var(--white); }
</style>
</head>
<body>
<div class="canvas">

  <section class="card card--back">
    <div class="wordmark">
      <div class="wordmark__row">
        <span class="wordmark__square"></span>
        <span class="wordmark__name">MERIDIAN</span>
      </div>
      <span class="wordmark__sub">REAL ESTATE</span>
    </div>
  </section>

  <section class="card card--front">
    <svg class="card__art" viewBox="0 0 560 320" width="560" height="320">
      <defs>
        <linearGradient id="photoTone" x1="0" y1="0" x2="0" y2="1">
          <stop offset="0" stop-color="#c9cbd6"/>
          <stop offset="1" stop-color="#2c3f86"/>
        </linearGradient>
        <linearGradient id="bandTone" x1="0" y1="0" x2="1" y2="1">
          <stop offset="0" stop-color="#1b275c"/>
          <stop offset=".5" stop-color="#26336e"/>
          <stop offset="1" stop-color="#141f4d"/>
        </linearGradient>
      </defs>
      <rect class="agent-photo" x="100" y="52" width="170" height="190" fill="url(#photoTone)" role="img" aria-label="Portrait photo of the agent in a blue suit"/>
      <polygon class="stripe" points="318,198 560,87 560,94 326,203" fill="#7a1a26"/>
      <polygon class="band" points="0,232 90,232 140,205 330,205 560,100 560,320 0,320" fill="url(#bandTone)"/>
    </svg>

    <div class="wordmark">
      <div class="wordmark__row">
        <span class="wordmark__square"></span>
        <span class="wordmark__name">MERIDIAN</span>
      </div>
      <span class="wordmark__sub">REAL ESTATE</span>
    </div>

    <ul class="contacts">
      <li>+852 2000 0147 <svg viewBox="0 0 24 24"><path d="M6.6 10.8a15 15 0 0 0 6.6 6.6l2.2-2.2a1 1 0 0 1 1-.25 11 11 0 0 0 3.6.6 1 1 0 0 1 1 1V20a1 1 0 0 1-1 1A17 17 0 0 1 3 4a1 1 0 0 1 1-1h3.5a1 1 0 0 1 1 1 11 11 0 0 0 .6 3.6 1 1 0 0 1-.25 1z"/></svg></li>
      <li>+852 2000 0158 <svg viewBox="0 0 24 24"><rect x="3" y="8" width="18" height="10" rx="2"/><rect x="7" y="3" width="10" height="5"/></svg></li>
      <li>info@meridianhomes.com <svg viewBox="0 0 24 24"><path d="M2 5h20v14H2z M4 7v.5l8 5 8-5V7l-8 5z" fill-rule="evenodd"/></svg></li>
      <li>www.meridianhomes.com <svg viewBox="0 0 24 24"><circle cx="12" cy="12" r="10"/></svg></li>
    </ul>

    <div class="agent">
      <p class="agent__name">DANIEL REYES</p>
      <p class="agent__role">Managing Director</p>
    </div>
    <p class="address">Via Monte Rosa,<br>118. 12040 Alba (CN)</p>
  </section>

</div>
</body>
</html>
```